Brightline Energy Product Distribution Brochure

We are looking to have our current brochure for our customers completely redesigned...the idea is to present the relevant information in an attractive way . Our website is brightlineenergyco.example where you can find more information about us. We have included a file with a rough idea of the page order and what each should include but feel free to adapt based on design. The example provided is only for context and doesnt have to be maintained. We will be using the brochure both digitally and in print form. As long as it reads easily and is eye catching, the design can be horizontal or vertical.Final deliverable should be indesign file.

"Our Brands" page: should be limited to one page (space being enough) where it has the header for each one (for example diesel generators) space for one or two lines of text and then the corresponding logos for each of the five categories
Updates

For those asking: the "our brands" page should be a single page layout where there is a header with the corresponding section and space for maybe one line of text followed by the two logos for that category. Each of the product pages should be similar in fashion to the one in the document attached: a photo of the product with some white space and space for the text to be included. We will be posting additional examples today

Target Market(s)

We want to present it to customers both digitally and in print so they can see our products

Industry/Entity Type

Power Generation

Font styles to use
Serif

Requirements
Must have
• Eye catching and able to present the information in a presentable fashion. Rest is up to you.
Nice to have
• Should incorporate the colors of our logo but can also add other depending on design

```html
<!DOCTYPE html>
<html lang="en">
<head>
<meta charset="utf-8">
<title>Brightline Energy – Product Brochure Spreads</title>
<link rel="stylesheet" href="https://fonts.googleapis.com/css2?family=Raleway:wght@300;400;600;700;800&family=Open+Sans:wght@400;600&display=swap">
<style>
  :root {
    --yellow: #f2c314;
    --yellow-deep: #e3b20c;
    --charcoal: #4a4646;
    --ink: #3a3a3a;
    --muted: #6b6b6b;
    --rule: #d9d9d9;
    --paper: #ffffff;
    --backdrop: #e7e7e7;
  }
  * { box-sizing: border-box; margin: 0; padding: 0; }
  html, body { width: 1200px; height: 453px; overflow: hidden; }
  body { background: var(--backdrop); font-family: "Open Sans", sans-serif; color: var(--ink); position: relative; }

  .spread { position: absolute; top: 37px; display: flex; box-shadow: 0 2px 8px rgba(0,0,0,.12); }
  .spread--stock-a { left: 40px; }
  .spread--stock-b { left: 632px; }

  .page { position: relative; width: 264px; height: 380px; background: var(--paper); overflow: hidden; }
  .page--left { box-shadow: inset -6px 0 8px -6px rgba(0,0,0,.12); }
  .page--right { box-shadow: inset 6px 0 8px -6px rgba(0,0,0,.12); }

  .band { position: absolute; left: 0; right: 0; }
  .band--yellow { top: 208px; height: 64px; background: var(--yellow); }
  .band--charcoal { top: 272px; bottom: 0; background: var(--charcoal); }

  .halo { position: absolute; left: 0; top: 0; }

  .running-head { position: absolute; top: 22px; left: 18px; right: 18px; height: 6px; display: flex; align-items: center; gap: 6px; }
  .running-head__bar { width: 26px; height: 4px; background: var(--yellow); }
  .running-head__line { flex: 1; height: 1px; background: var(--rule); }
  .running-head__label { font-family: "Raleway", sans-serif; font-size: 5.5px; letter-spacing: .3px; color: var(--muted); }

  .brand-tag { position: absolute; top: 17px; display: flex; align-items: center; gap: 3px; background: var(--paper); padding: 0 3px; }
  .page--left .brand-tag { right: 18px; }
  .page--right .brand-tag { left: 22px; }
  .brand-tag__square { width: 8px; height: 8px; background: var(--yellow); }
  .brand-tag__name { font-family: "Raleway", sans-serif; font-weight: 700; font-size: 5.5px; letter-spacing: .2px; color: var(--ink); text-transform: uppercase; }

  .brand-mark { position: absolute; right: 22px; top: 178px; display: flex; align-items: center; gap: 4px; }
  .brand-mark__square { width: 14px; height: 14px; background: var(--yellow); }
  .brand-mark__name { font-family: "Raleway", sans-serif; font-weight: 700; font-size: 6.5px; color: var(--ink); text-transform: uppercase; }

  .page-title { position: absolute; left: 22px; top: 52px; font-family: "Raleway", sans-serif; font-weight: 300; font-size: 17px; letter-spacing: .2px; color: var(--ink); text-transform: uppercase; }

  .section-head { position: absolute; left: 22px; top: 85px; display: flex; align-items: center; gap: 4px; font-family: "Raleway", sans-serif; font-weight: 800; font-size: 8px; color: var(--ink); text-transform: uppercase; }
  .section-head svg { display: block; }

  .intro { position: absolute; left: 22px; top: 99px; width: 108px; font-size: 4.6px; line-height: 1.45; color: var(--muted); text-align: justify; }

  .points { position: absolute; left: 136px; top: 99px; width: 104px; list-style: none; }
  .points li { display: flex; gap: 4px; margin-bottom: 4px; font-size: 4.6px; line-height: 1.45; color: var(--muted); }
  .points__num { flex: none; width: 6px; height: 6px; background: var(--yellow); color: var(--paper); font-weight: 600; font-size: 4.2px; line-height: 6px; text-align: center; }

  .product { position: absolute; left: 132px; top: 290px; transform: translate(-50%, -50%); }
  .product--switch { width: 46px; height: 90px; background: linear-gradient(90deg, #b7b9bb, #dfe0e1 40%, #a9abad); }
  .product--gensets { width: 104px; height: 44px; background: linear-gradient(180deg, #6a6a6a, #2f2f2f); }
  .product--regulator { width: 58px; height: 66px; background: linear-gradient(160deg, #2b2b2b, #1b1b1b 70%, #3a6fb3); }
  .product--controller { width: 68px; height: 50px; border-radius: 4px; background: linear-gradient(180deg, #2e2e2e, #161616); }

  .folio { position: absolute; bottom: 9px; display: flex; align-items: center; gap: 5px; font-size: 4.4px; color: #e8e8e8; }
  .page--left .folio { left: 14px; }
  .page--right .folio { right: 14px; }
  .folio__rule { width: 14px; height: 1px; background: var(--yellow); }
</style>
</head>
<body>

<!-- Spread: Transfer Switches / Our Distributors -->
<section class="spread spread--stock-a">
  <article class="page page--left">
    <div class="band band--yellow"></div>
    <div class="band band--charcoal"></div>
    <svg class="halo" width="264" height="380" aria-hidden="true">
      <circle cx="132" cy="290" r="132" fill="rgba(0,0,0,0.07)"/>
      <circle cx="132" cy="290" r="100" fill="var(--yellow)"/>
      <circle cx="132" cy="290" r="92" fill="var(--yellow-deep)" opacity=".35"/>
      <circle cx="132" cy="290" r="74" fill="var(--paper)"/>
    </svg>
    <div class="running-head"><span class="running-head__bar"></span><span class="running-head__label">OUR STOCK</span><span class="running-head__line"></span></div>
    <div class="brand-tag"><span class="brand-tag__square"></span><span class="brand-tag__name">Brightline Energy</span></div>
    <h1 class="page-title">Transfer Switches</h1>
    <h2 class="section-head"><svg width="8" height="8" viewBox="0 0 8 8"><circle cx="4" cy="4" r="4" fill="var(--yellow)"/><path d="M3 2l2 2-2 2" stroke="#fff" stroke-width="1" fill="none"/></svg>Transfer Switches</h2>
    <p class="intro">Our team supplies dependable equipment for standby and prime power needs across many industries. Every unit is inspected, tested and documented before shipping, so your project stays on schedule and your site stays powered when it matters most.</p>
    <ol class="points">
      <li><span class="points__num">1</span>Wide selection of units ready to ship from stock.</li>
      <li><span class="points__num">2</span>Technical support from experienced engineers for sizing and installation.</li>
      <li><span class="points__num">3</span>Fast delivery to job sites across the country.</li>
    </ol>
    <div class="product product--switch" role="img" aria-label="Photo of a grey automatic transfer switch cabinet"></div>
    <footer class="folio"><span>12</span><span class="folio__rule"></span><span>brightlineenergyco.example</span></footer>
  </article>

  <article class="page page--right">
    <div class="band band--yellow"></div>
    <div class="band band--charcoal"></div>
    <svg class="halo" width="264" height="380" aria-hidden="true">
      <circle cx="132" cy="290" r="132" fill="rgba(0,0,0,0.07)"/>
      <circle cx="132" cy="290" r="100" fill="var(--yellow)"/>
      <circle cx="132" cy="290" r="92" fill="var(--yellow-deep)" opacity=".35"/>
      <circle cx="132" cy="290" r="74" fill="var(--paper)"/>
    </svg>
    <div class="running-head"><span class="running-head__line"></span><span class="running-head__label">OUR STOCK</span><span class="running-head__bar"></span></div>
    <div class="brand-tag"><span class="brand-tag__square"></span><span class="brand-tag__name">Brightline Energy</span></div>
    <h1 class="page-title">Our Distributors</h1>
    <h2 class="section-head"><svg width="8" height="8" viewBox="0 0 8 8"><circle cx="4" cy="4" r="4" fill="var(--yellow)"/><path d="M3 2l2 2-2 2" stroke="#fff" stroke-width="1" fill="none"/></svg>Our Distributors</h2>
    <p class="intro">Our team supplies dependable equipment for standby and prime power needs across many industries. Every unit is inspected, tested and documented before shipping, so your project stays on schedule and your site stays powered when it matters most.</p>
    <ol class="points">
      <li><span class="points__num">1</span>Wide selection of units ready to ship from stock.</li>
      <li><span class="points__num">2</span>Technical support from experienced engineers for sizing and installation.</li>
      <li><span class="points__num">3</span>Fast delivery to job sites across the country.</li>
    </ol>
    <div class="brand-mark"><span class="brand-mark__square"></span><span class="brand-mark__name">Brightline Energy</span></div>
    <div class="product product--gensets" role="img" aria-label="Photo of a group of diesel generator sets and engines"></div>
    <footer class="folio"><span>brightlineenergyco.example</span><span class="folio__rule"></span><span>13</span></footer>
  </article>
</section>

<!-- Spread: Alternator Parts / Controllers -->
<section class="spread spread--stock-b">
  <article class="page page--left">
    <div class="band band--yellow"></div>
    <div class="band band--charcoal"></div>
    <svg class="halo" width="264" height="380" aria-hidden="true">
      <circle cx="132" cy="290" r="132" fill="rgba(0,0,0,0.07)"/>
      <circle cx="132" cy="290" r="100" fill="var(--yellow)"/>
      <circle cx="132" cy="290" r="92" fill="var(--yellow-deep)" opacity=".35"/>
      <circle cx="132" cy="290" r="74" fill="var(--paper)"/>
    </svg>
    <div class="running-head"><span class="running-head__bar"></span><span class="running-head__label">OUR STOCK</span><span class="running-head__line"></span></div>
    <div class="brand-tag"><span class="brand-tag__square"></span><span class="brand-tag__name">Brightline Energy</span></div>
    <h1 class="page-title">Alternator Parts</h1>
    <h2 class="section-head"><svg width="8" height="8" viewBox="0 0 8 8"><circle cx="4" cy="4" r="4" fill="var(--yellow)"/><path d="M3 2l2 2-2 2" stroke="#fff" stroke-width="1" fill="none"/></svg>Alternator Parts</h2>
    <p class="intro">Our team supplies dependable equipment for standby and prime power needs across many industries. Every unit is inspected, tested and documented before shipping, so your project stays on schedule and your site stays powered when it matters most.</p>
    <ol class="points">
      <li><span class="points__num">1</span>Wide selection of units ready to ship from stock.</li>
      <li><span class="points__num">2</span>Technical support from experienced engineers for sizing and installation.</li>
      <li><span class="points__num">3</span>Fast delivery to job sites across the country.</li>
    </ol>
    <div class="product product--regulator" role="img" aria-label="Photo of an automatic voltage regulator board"></div>
    <footer class="folio"><span>10</span><span class="folio__rule"></span><span>brightlineenergyco.example</span></footer>
  </article>

  <article class="page page--right">
    <div class="band band--yellow"></div>
    <div class="band band--charcoal"></div>
    <svg class="halo" width="264" height="380" aria-hidden="true">
      <circle cx="132" cy="290" r="132" fill="rgba(0,0,0,0.07)"/>
      <circle cx="132" cy="290" r="100" fill="var(--yellow)"/>
      <circle cx="132" cy="290" r="92" fill="var(--yellow-deep)" opacity=".35"/>
      <circle cx="132" cy="290" r="74" fill="var(--paper)"/>
    </svg>
    <div class="running-head"><span class="running-head__line"></span><span class="running-head__label">OUR STOCK</span><span class="running-head__bar"></span></div>
    <div class="brand-tag"><span class="brand-tag__square"></span><span class="brand-tag__name">Brightline Energy</span></div>
    <h1 class="page-title">Controllers</h1>
    <h2 class="section-head"><svg width="8" height="8" viewBox="0 0 8 8"><circle cx="4" cy="4" r="4" fill="var(--yellow)"/><path d="M3 2l2 2-2 2" stroke="#fff" stroke-width="1" fill="none"/></svg>Controllers</h2>
    <p class="intro">Our team supplies dependable equipment for standby and prime power needs across many industries. Every unit is inspected, tested and documented before shipping, so your project stays on schedule and your site stays powered when it matters most.</p>
    <ol class="points">
      <li><span class="points__num">1</span>Wide selection of units ready to ship from stock.</li>
      <li><span class="points__num">2</span>Technical support from experienced engineers for sizing and installation.</li>
      <li><span class="points__num">3</span>Fast delivery to job sites across the country.</li>
    </ol>
    <div class="brand-mark"><span class="brand-mark__square"></span><span class="brand-mark__name">Brightline Energy</span></div>
    <div class="product product--controller" role="img" aria-label="Photo of a generator control module with display and buttons"></div>
    <footer class="folio"><span>brightlineenergyco.example</span><span class="folio__rule"></span><span>11</span></footer>
  </article>
</section>

</body>
</html>
```